Stylish new business card needed!

Hello everyone! I am in need of a new business card design for an alarm company here in Hurricane WV. I have all fonts, color codes and logos provided for you use! We are a young company and like the style of a clean sleek looking business card. Would like it double sided, one side holding the logo and the other with your design!
Target Market(s)
The people that are looking for the newest tech for home automation and security
Industry/Entity Type
Alarm services; Home automation
Contact Information for Business Card
Name of person; position (Sales; Installer); Phone Number (555.418.7260); Employee cell Number; Website (www.GuardedByVelk.example); Employee Email; Double sided
Look and feel
Each slider illustrates characteristics of the customer's brand and the style your logo design should communicate.

```html
<!DOCTYPE html>
<html lang="en">
<head>
<meta charset="utf-8">
<title>Velk Business Card</title>
<link href="https://fonts.googleapis.com/css2?family=Arimo:wght@400;700&display=swap" rel="stylesheet">
<style>
  :root {
    --orange: #f28c45;
    --gray: #9b9b9b;
    --gray-dark: #8a8a8a;
    --ink: #111111;
    --paper: #ffffff;
    --backdrop: #e9e9e9;
  }
  * { margin: 0; padding: 0; box-sizing: border-box; }
  html, body {
    width: 1200px; height: 780px; overflow: hidden;
    background: var(--backdrop);
    font-family: "Arimo", Arial, sans-serif;
  }
  .canvas {
    position: relative; width: 1200px; height: 780px;
  }
  .card {
    position: absolute; left: 290px; width: 620px; height: 354px;
    border-radius: 26px; overflow: hidden;
    box-shadow: 0 5px 0 var(--orange), 0 10px 24px rgba(0,0,0,.18);
  }
  .card-back { top: 24px; background: var(--gray); }
  .card-front { top: 400px; background: var(--paper); }

  /* back side */
  .back-pattern {
    position: absolute; inset: 0;
    background: linear-gradient(135deg, #a4a4a4 0%, #959595 50%, #a0a0a0 100%);
  }
  .back-name {
    position: absolute; right: 70px; top: 150px;
    color: var(--paper); font-weight: 400; font-size: 34px; letter-spacing: 1px;
  }

  /* front side */
  .brand-name {
    position: absolute; left: 60px; top: 110px;
    color: var(--gray); font-weight: 700; font-size: 104px; letter-spacing: 2px; line-height: 1;
  }
  .divider {
    position: absolute; left: 332px; top: 58px; width: 2px; height: 196px; background: var(--ink);
  }
  .contact-block { position: absolute; left: 360px; top: 66px; }
  .person-name { font-size: 29px; font-weight: 700; line-height: 1; }
  .person-first { color: var(--orange); }
  .person-last { color: var(--gray); }
  .person-role { margin-top: 6px; font-size: 15px; font-weight: 700; color: var(--ink); }
  .contact-list { list-style: none; margin-top: 22px; }
  .contact-list li {
    display: flex; align-items: center; gap: 10px;
    font-size: 14.5px; color: var(--ink); line-height: 22px;
  }
  .contact-list svg { width: 14px; height: 14px; flex: none; }

  .band-orange {
    position: absolute; left: 0; top: 308px; width: 372px; height: 20px; background: var(--orange);
  }
  .band-gray {
    position: absolute; left: 462px; top: 262px; width: 158px; height: 18px; background: var(--gray);
  }
  .corner-name {
    position: absolute; left: 380px; top: 284px;
    color: var(--gray-dark); font-weight: 700; font-size: 40px; line-height: 1;
  }
</style>
</head>
<body>
<main class="canvas">
  <section class="card card-back" aria-label="Card back">
    <div class="back-pattern" role="img" aria-label="Repeating brand wordmark pattern in tonal grey"></div>
    <span class="back-name">Velk</span>
  </section>

  <section class="card card-front" aria-label="Card front">
    <span class="brand-name">Velk</span>
    <div class="divider"></div>

    <div class="contact-block">
      <p class="person-name"><span class="person-first">Dana</span> <span class="person-last">Morrow</span></p>
      <p class="person-role">Sales; Installer</p>
      <ul class="contact-list">
        <li>
          <svg viewBox="0 0 24 24" aria-hidden="true"><path fill="var(--orange)" d="M6.6 10.8a15 15 0 0 0 6.6 6.6l2.2-2.2c.3-.3.7-.4 1-.2 1.1.4 2.3.6 3.6.6.6 0 1 .4 1 1V20c0 .6-.4 1-1 1A17 17 0 0 1 3 4c0-.6.4-1 1-1h3.5c.6 0 1 .4 1 1 0 1.3.2 2.5.6 3.6.1.3 0 .7-.2 1z"/></svg>
          555.418.7260
        </li>
        <li>
          <svg viewBox="0 0 24 24" aria-hidden="true"><rect x="6" y="2" width="12" height="20" rx="2" fill="none" stroke="var(--orange)" stroke-width="2"/><circle cx="12" cy="18" r="1.2" fill="var(--orange)"/></svg>
          555.902.3318
        </li>
        <li>
          <svg viewBox="0 0 24 24" aria-hidden="true"><circle cx="12" cy="12" r="9" fill="none" stroke="var(--orange)" stroke-width="2"/><path d="M3 12h18M12 3c3 3 3 15 0 18M12 3c-3 3-3 15 0 18" fill="none" stroke="var(--orange)" stroke-width="1.6"/></svg>
          www.GuardedByVelk.example
        </li>
        <li>
          <svg viewBox="0 0 24 24" aria-hidden="true"><rect x="3" y="5" width="18" height="14" rx="1.5" fill="var(--orange)"/><path d="M3.5 6l8.5 7 8.5-7" fill="none" stroke="var(--paper)" stroke-width="1.8"/></svg>
          info@GuardedByVelk.example
        </li>
      </ul>
    </div>

    <div class="band-orange"></div>
    <span class="corner-name">Velk</span>
    <div class="band-gray"></div>
  </section>
</main>
</body>
</html>
```